MS Word Template for Proposals and RFP

Looking for a nice looking graphic template in MS Word. We will use this to make proposals and answer RFPs. Looking for something that will match our company brand, but give a fresh, up-to-date look and feel. There are a few pictures of a template I like. I don't necessarily like that logo - looks too "kid like" for business, but I really like how clean and organized it is. Most proposals and RFP responses are looooooonnnngggg and boring - need something that someone can look through and find what they are looking for quickly and easily.
Updates

Can't wait to see your designs!

Target Market(s)

School districts and other governmental employers

Industry/Entity Type

Business

Requirements
Must have
• Must include sample table of contents, section dividers, charts, graphs and tables that we customized based on the content. The goal is for it to look simple, clean, compelling - organized so it's easy to read, easy to find your way around - good headers, charts, flow charts, tables.... etc. Looking to have 5-10 template pages that we can use to put together and entire portfolio.
Should not have
• No "cutsie" comic sans/apple for the teacher kind of stuff - we are selling employee benefits to schools and other governmental entities. Should be more serious and conservative but also look compelling and draw in the reader.

```html
<!DOCTYPE html>
<html lang="en">
<head>
<meta charset="utf-8">
<title>Contents – Table Data</title>
<link rel="stylesheet" href="https://fonts.googleapis.com/css2?family=Rokkitt:wght@300;400&family=Open+Sans:wght@400&display=swap">
<style>
  :root {
    --brand-blue: #5b7fc4;
    --heading-blue: #5a7fc2;
    --band-grey: #c9c9c9;
    --text: #555555;
    --paper: #ffffff;
    --grid: #9a9a9a;
    --retail: #4a8fd0;
    --dining: #aecdee;
    --culture: #4f93cc;
    --undeveloped: #1c6cb8;
    --bar-shadow: #3d3d3d;
  }
  * { margin: 0; padding: 0; box-sizing: border-box; }
  html, body { width: 900px; height: 1200px; overflow: hidden; background: var(--paper); }
  .page { position: relative; width: 900px; height: 1200px; overflow: hidden; font-family: "Rokkitt", Georgia, serif; }

  .page-header { position: absolute; top: 0; left: 0; width: 900px; height: 63px; }
  .page-header svg { position: absolute; inset: 0; }
  .page-title {
    position: absolute; right: 16px; top: 2px;
    font-family: "Rokkitt", Georgia, serif; font-weight: 300;
    font-size: 46px; color: var(--paper); line-height: 60px;
  }

  .intro { position: absolute; left: 33px; top: 102px; width: 834px; }
  .section-heading {
    font-weight: 300; font-size: 30px; color: var(--heading-blue); line-height: 38px; margin-bottom: 2px;
  }
  .intro p {
    font-weight: 300; font-size: 20px; line-height: 34.5px; color: var(--text);
    text-align: justify; hyphens: auto; -webkit-hyphens: auto;
  }

  .chart { position: absolute; left: 0; top: 440px; width: 900px; height: 460px; }
  .chart text { font-family: "Open Sans", Arial, sans-serif; }

  .page-footer { position: absolute; left: 0; bottom: 0; width: 900px; height: 51px; background: var(--brand-blue); }
  .footer-brand {
    position: absolute; left: 18px; top: 0; width: 315px; height: 51px; background: var(--paper);
    display: flex; align-items: center; justify-content: center;
    font-family: "Rokkitt", Georgia, serif; font-weight: 400; font-size: 23px;
    color: var(--brand-blue); letter-spacing: 0.5px;
  }
  .footer-url {
    position: absolute; right: 15px; top: 0; line-height: 51px;
    font-family: "Rokkitt", Georgia, serif; font-weight: 300; font-size: 21px; color: var(--paper);
  }
</style>
</head>
<body>
<div class="page">
  <header class="page-header">
    <svg width="900" height="63" viewBox="0 0 900 63">
      <polygon points="0,0 138,0 86,63 0,63" fill="var(--band-grey)"/>
      <polygon points="142,0 900,0 900,63 90,63" fill="var(--brand-blue)"/>
    </svg>
    <h1 class="page-title">Contents</h1>
  </header>

  <section class="intro">
    <h2 class="section-heading">Table Data</h2>
    <p>This template uses a few tables to create the page structure that follows. A host table consisting of just two columns and one row enables the sidebar content to sit beside the text, tables, and diagram on the left without any complicated positioning required. Nested tables (a nested table is just one table inside another) in both the left and right column enable you to place text beside the process graphic, provide the small financial table below left, and provide the sidebar table with a separate cell for the heading text.</p>
  </section>

  <figure class="chart">
    <svg width="900" height="460" viewBox="0 0 900 460" role="img" aria-label="Bar chart of retail, dining, culture and undeveloped values for 2010 and 2011">
      <g class="gridlines" stroke="var(--grid)" stroke-width="1" stroke-dasharray="4 3">
        <line x1="181" y1="26.5" x2="720" y2="26.5"/>
        <line x1="181" y1="77" x2="720" y2="77"/>
        <line x1="181" y1="127" x2="720" y2="127"/>
        <line x1="181" y1="177" x2="720" y2="177"/>
        <line x1="181" y1="227.5" x2="720" y2="227.5"/>
        <line x1="181" y1="277.5" x2="720" y2="277.5"/>
      </g>
      <g class="bar-shadows" fill="var(--bar-shadow)" opacity="0.75">
        <rect x="207" y="111" width="56" height="6"/>
        <rect x="263" y="131" width="56" height="6"/>
        <rect x="319" y="221" width="56" height="6"/>
        <rect x="375" y="171" width="56" height="6"/>
        <rect x="474" y="30" width="56" height="6"/>
        <rect x="530" y="81" width="56" height="6"/>
        <rect x="586" y="176" width="56" height="6"/>
        <rect x="642" y="221" width="56" height="6"/>
      </g>
      <g class="bars">
        <rect x="205" y="117" width="56" height="211" fill="var(--retail)"/>
        <rect x="261" y="137" width="56" height="191" fill="var(--dining)"/>
        <rect x="317" y="227" width="56" height="101" fill="var(--culture)"/>
        <rect x="373" y="177" width="56" height="151" fill="var(--undeveloped)"/>
        <rect x="472" y="36" width="56" height="292" fill="var(--retail)"/>
        <rect x="528" y="87" width="56" height="241" fill="var(--dining)"/>
        <rect x="584" y="182" width="56" height="146" fill="var(--culture)"/>
        <rect x="640" y="227" width="56" height="101" fill="var(--undeveloped)"/>
      </g>
      <g class="bar-values" fill="var(--paper)" font-size="15" text-anchor="middle">
        <text x="233" y="139">4.2</text>
        <text x="289" y="159">3.8</text>
        <text x="345" y="249">2.0</text>
        <text x="401" y="199">3.0</text>
        <text x="500" y="58">5.8</text>
        <text x="556" y="109">4.8</text>
        <text x="612" y="204">2.9</text>
        <text x="668" y="249">2.0</text>
      </g>
      <g class="axis" stroke="#888" stroke-width="1">
        <line x1="181" y1="328" x2="720" y2="328"/>
        <line x1="181" y1="328" x2="181" y2="335"/>
        <line x1="450" y1="328" x2="450" y2="335"/>
        <line x1="720" y1="328" x2="720" y2="335"/>
      </g>
      <g class="categories" fill="#333" font-size="13" text-anchor="middle">
        <text x="316" y="351">2010</text>
        <text x="585" y="351">2011</text>
      </g>
      <g class="legend" font-size="11.5" fill="#333">
        <rect x="243" y="420" width="8" height="8" fill="var(--retail)"/>
        <text x="254" y="428">RETAIL</text>
        <rect x="343" y="420" width="8" height="8" fill="var(--dining)"/>
        <text x="354" y="428">DINING</text>
        <rect x="442" y="420" width="8" height="8" fill="var(--culture)"/>
        <text x="453" y="428">CULTURE</text>
        <rect x="543" y="420" width="8" height="8" fill="var(--undeveloped)"/>
        <text x="554" y="428">UNDEVELOPED</text>
      </g>
    </svg>
  </figure>

  <footer class="page-footer">
    <div class="footer-brand">MERIDIAN BENEFIT GROUP</div>
    <div class="footer-url">www.meridianbenefit.com</div>
  </footer>
</div>
</body>
</html>
```